Kestrelbrook Student Accomodation needs a business card design

Hi Guys,

We are a Student Accommodation company in Australia. We already have a logo which I will submit.

I will require the design of the business cards from you.

I am after something that looks clean, modern and that people feel interested and actually want to contact us.

We would like to see designs that are innovative.

On the business cards I will require to have:

Employee Name
Position
Phone number
Email
Facebook page

I hope you can help me with this project guys as I have heard really good things from you.

```html
<!DOCTYPE html>
<html lang="en">
<head>
<meta charset="utf-8">
<title>Kestrelbrook Student Accomodation – Business Card</title>
<link rel="stylesheet" href="https://fonts.googleapis.com/css2?family=Open+Sans:wght@400;600;700&display=swap">
<style>
  :root {
    --green: #0b8e45;
    --yellow: #f5b72e;
    --white: #ffffff;
    --ink: #1f1f1f;
    --stage: #e9e6e1;
    --shadow: rgba(0, 0, 0, 0.28);
  }
  * { box-sizing: border-box; margin: 0; padding: 0; }
  html, body {
    width: 1200px;
    height: 765px;
    overflow: hidden;
  }
  body {
    background: var(--stage);
    font-family: "Open Sans", Arial, sans-serif;
    position: relative;
  }
  .card {
    position: absolute;
    width: 596px;
    height: 341px;
    background: var(--white);
    box-shadow: 6px 8px 18px var(--shadow);
    overflow: hidden;
  }
  .card--front { left: 102px; top: 52px; z-index: 2; }
  .card--back  { left: 519px; top: 352px; z-index: 1; }

  .brand {
    position: absolute;
    display: flex;
    align-items: center;
    gap: 10px;
    color: var(--green);
    font-weight: 700;
    line-height: 1.1;
  }
  .brand__mark {
    width: 14px;
    height: 14px;
    background: var(--yellow);
    flex: none;
  }
  .card--front .brand {
    left: 0; right: 0; top: 52px;
    justify-content: center;
    font-size: 24px;
  }
  .card--back .brand {
    left: 0; right: 0; top: 0; bottom: 0;
    justify-content: center;
    font-size: 34px;
  }
  .card--back .brand__mark { width: 22px; height: 22px; }

  .person {
    position: absolute;
    left: 25px;
    top: 166px;
    color: var(--green);
    line-height: 1.3;
  }
  .person__name { font-size: 21px; font-weight: 700; }
  .person__position { font-size: 16px; font-weight: 600; color: var(--yellow); }

  .contacts {
    position: absolute;
    left: 25px;
    top: 200px;
    list-style: none;
    font-size: 15.5px;
    color: var(--ink);
    z-index: 2;
  }
  .contacts li {
    display: flex;
    align-items: center;
    gap: 8px;
    height: 26px;
  }
  .contacts svg { width: 13px; height: 13px; flex: none; }

  .wave {
    position: absolute;
    left: 0;
    bottom: 0;
    width: 596px;
    height: 90px;
    z-index: 1;
  }
</style>
</head>
<body>
  <section class="card card--front" aria-label="Business card front">
    <div class="brand">
      <span class="brand__mark"></span>
      <span class="brand__name">Kestrelbrook Student Accomodation</span>
    </div>

    <div class="person">
      <span class="person__name">Employee Name,</span>
      <span class="person__position">Position</span>
    </div>

    <ul class="contacts">
      <li>
        <svg viewBox="0 0 16 16" aria-hidden="true"><path fill="var(--green)" d="M3.5 1.5l2.5 3-1.5 1.6a9 9 0 0 0 5.4 5.4L11.5 10l3 2.5-1.6 2.2C7 14.5 1.5 9 1.3 3.1z"/></svg>
        123-456-7890
      </li>
      <li>
        <svg viewBox="0 0 16 16" aria-hidden="true"><rect x="1" y="3" width="14" height="10" rx="1" fill="var(--green)"/><path d="M1.5 3.8L8 9l6.5-5.2" fill="none" stroke="#fff" stroke-width="1.3"/></svg>
        info@kestrelbrook.com
      </li>
      <li>
        <svg viewBox="0 0 16 16" aria-hidden="true"><rect x="1" y="1" width="14" height="14" fill="var(--green)"/></svg>
        /kestrelbrookstay
      </li>
    </ul>

    <svg class="wave" viewBox="0 0 596 90" preserveAspectRatio="none" aria-hidden="true">
      <path d="M0 36 C120 56 230 70 330 52 C420 36 500 22 596 40 L596 90 L0 90 Z" fill="var(--yellow)"/>
      <path d="M0 46 C120 66 230 80 330 62 C420 46 500 32 596 48 L596 90 L0 90 Z" fill="var(--white)"/>
      <path d="M0 54 C130 74 240 76 340 60 C430 46 510 36 596 52 L596 90 L0 90 Z" fill="var(--green)"/>
    </svg>
  </section>

  <section class="card card--back" aria-label="Business card back">
    <div class="brand">
      <span class="brand__mark"></span>
      <span class="brand__name">Kestrelbrook</span>
    </div>
  </section>
</body>
</html>
```